Velvet Lantern rebranding my business with a new business card

I have my new logo and now I need a refresher on my business cards. I really want something fun and fresh. I like black background or anything to make the color pop.
Logo
Name: Velvet Lantern
Contact Info as stated below:
Mira Pellow
555-013-4762
Logo
Name: Velvet Lantern
Mira Pellow
555-013-4762
fb.me/VelvetLanternbyMira
Instagram: @VelvetLanternbyMira

Industry/Entity Type

Business

Contact Information for Business Card

double-sided. Logo on one side. Contact info on the other.

Requirements
Must have
• Logo
• Name: Velvet Lantern
• Contact Info as stated below:
• Mira Pellow
• 555-013-4762
• fb.me/VelvetLanternbyMira
• fb.me/VelvetLanternbyMira

```html
<!DOCTYPE html>
<html lang="en">
<head>
<meta charset="utf-8">
<title>Velvet Lantern – Business Card</title>
<link href="https://fonts.googleapis.com/css2?family=Roboto:wght@400;500&family=Roboto+Condensed:wght@700&display=swap" rel="stylesheet">
<style>
  :root {
    --backdrop: #ece8e4;
    --card-pink: #f0a5b4;
    --card-white: #f4f4f4;
    --ink: #2b2b2b;
    --ink-soft: #6e5a5f;
    --accent-pink: #f2a9b9;
    --ring-pink: #f0a0b3;
    --edge-dark: #141414;
  }
  * { margin: 0; padding: 0; box-sizing: border-box; }
  html, body {
    width: 1200px; height: 960px; overflow: hidden;
    background: var(--backdrop);
  }
  .canvas { position: relative; width: 1200px; height: 960px; }

  .card {
    position: absolute;
    border-radius: 18px;
    box-shadow: 0 6px 14px rgba(0,0,0,0.25);
  }

  /* Logo side */
  .card-front {
    left: 320px; top: 100px; width: 605px; height: 350px;
    background: var(--card-pink);
  }
  .front-brand {
    position: absolute; left: 0; right: 0; top: 150px;
    text-align: center;
    font-family: "Roboto", sans-serif; font-weight: 500;
    font-size: 34px; color: var(--ink-soft);
  }
  .front-web {
    position: absolute; left: 0; right: 0; top: 298px;
    text-align: center;
    font-family: "Roboto", sans-serif; font-size: 14px;
    letter-spacing: 5.5px; color: var(--ink-soft);
  }

  /* Contact side */
  .card-back {
    left: 320px; top: 493px; width: 600px; height: 340px;
    background: var(--card-white);
    border-bottom: 8px solid var(--edge-dark);
    overflow: hidden;
  }
  .card-back::after {
    content: ""; position: absolute; left: 0; right: 0; bottom: 0;
    height: 5px; background: var(--accent-pink);
  }
  .name-tab {
    position: absolute; left: 0; top: 198px;
    width: 14px; height: 26px;
    background: var(--accent-pink);
    border-radius: 0 8px 8px 0;
  }
  .person-name {
    position: absolute; left: 32px; top: 197px;
    font-family: "Roboto Condensed", sans-serif; font-weight: 700;
    font-size: 22px; color: var(--ink);
  }
  .contact-list {
    position: absolute; left: 34px; top: 244px;
    list-style: none;
    font-family: "Roboto", sans-serif; font-size: 14px; color: var(--ink);
  }
  .contact-list li {
    display: flex; align-items: center; gap: 8px; height: 19.5px;
  }
  .contact-list svg { width: 13px; height: 13px; flex: none; }

  .brand-seal {
    position: absolute; left: 337px; top: 28px;
    width: 230px; height: 230px;
  }
  .seal-name {
    position: absolute; inset: 0;
    display: flex; align-items: center; justify-content: center;
    text-align: center;
    font-family: "Roboto", sans-serif; font-weight: 500;
    font-size: 26px; line-height: 1.15; color: var(--ink-soft);
  }
</style>
</head>
<body>
<main class="canvas">

  <section class="card card-front" aria-label="Logo side">
    <div class="front-brand">Velvet Lantern</div>
    <div class="front-web">www.velvetlantern.com</div>
  </section>

  <section class="card card-back" aria-label="Contact side">
    <div class="brand-seal">
      <svg width="230" height="230" viewBox="0 0 230 230" aria-hidden="true">
        <circle cx="115" cy="115" r="113" fill="#fff" stroke="#111" stroke-width="2"/>
        <circle cx="115" cy="115" r="105" fill="none" stroke="var(--ring-pink)" stroke-width="2.5"/>
        <circle cx="115" cy="115" r="100" fill="none" stroke="var(--ring-pink)" stroke-width="1"/>
      </svg>
      <div class="seal-name">Velvet<br>Lantern</div>
    </div>

    <span class="name-tab"></span>
    <h1 class="person-name">MIRA PELLOW</h1>

    <ul class="contact-list">
      <li>
        <svg viewBox="0 0 16 16" aria-hidden="true"><path fill="#2b2b2b" d="M3.6 1.2l2.3 2.6-1.4 1.8c.9 2 2.4 3.6 4.5 4.6l1.8-1.4 2.6 2.3-1.3 2.6C7.4 13.6 2.4 8.6 1 3.9z"/></svg>
        555-013-4762
      </li>
      <li>
        <svg viewBox="0 0 16 16" aria-hidden="true"><circle cx="8" cy="8" r="6.5" fill="none" stroke="#2b2b2b" stroke-width="2"/><path d="M1.5 8h13M8 1.5c-3 3-3 10 0 13M8 1.5c3 3 3 10 0 13" fill="none" stroke="#2b2b2b" stroke-width="1.2"/></svg>
        www.velvetlantern.com
      </li>
      <li>
        <svg viewBox="0 0 16 16" aria-hidden="true"><rect x="1" y="1" width="14" height="14" rx="2" fill="#2b2b2b"/></svg>
        fb.me/VelvetLanternbyMira
      </li>
    </ul>
  </section>

</main>
</body>
</html>
```